Pepper & Palm Business Card FUN & EXCITING

Here is the Information for the Card:
Jaswinder Bains (Ravi)
E: RaviBains@postlark.com
C: (480) 555-0147
www.PepperPalmLV.com

We don't want traditional Indian cliche, We a playful bold and fun business card.

Files: https://files.cloudvessel.net/share/folders/7TqRmXpZ2vKa9LwBn4YcHd3JsEf6UoGi?usp=share_link

https://files.cloudvessel.net/share/folders/4MzXaQ8rTw2YbNcVk6PsLe5GhJdR3FoU?usp=share_link

Target Market(s)

Las Vegas Local Restaurant

Industry/Entity Type

Indian Restaurant

Contact Information for Business Card

Name, Email, Cell Phone, Company Logo

```html
<!DOCTYPE html>
<html lang="en">
<head>
<meta charset="utf-8">
<title>Pepper &amp; Palm Business Card</title>
<link rel="stylesheet" href="https://fonts.googleapis.com/css2?family=Montserrat:wght@300;400;600;800&display=swap">
<style>
  :root {
    --page: #2a2a2a;
    --card: #1e1e1e;
    --orange: #ee7a26;
    --white: #ffffff;
  }
  * { margin: 0; padding: 0; box-sizing: border-box; }
  html, body { width: 1200px; height: 1108px; overflow: hidden; background: var(--page); }
  body { position: relative; font-family: "Montserrat", sans-serif; color: var(--white); }

  .card {
    position: absolute;
    background: var(--card);
    border-radius: 20px;
    overflow: hidden;
  }
  .card-front { left: 262px; top: 130px; width: 708px; height: 432px; }
  .card-back  { left: 260px; top: 603px; width: 708px; height: 447px; }

  .brand-front {
    position: absolute; left: 0; right: 0; top: 184px;
    text-align: center;
    font-weight: 800; font-size: 46px; letter-spacing: 1px;
    color: var(--white);
  }

  .brand-back {
    position: absolute; left: 104px; top: 150px; width: 150px;
    text-align: center;
    font-weight: 800; font-size: 32px; line-height: 1.15;
    color: var(--white);
  }

  .divider {
    position: absolute; left: 304px; top: 149px;
    width: 2px; height: 157px; background: var(--orange);
  }

  .contact { position: absolute; left: 317px; top: 144px; }
  .contact-name {
    font-weight: 600; font-size: 27px; color: var(--orange); white-space: nowrap;
  }
  .contact-role {
    display: inline-block; margin-top: 0px;
    font-weight: 400; font-size: 17px; color: var(--white);
    border-bottom: 2px solid var(--orange); line-height: 1.15;
  }
  .contact-list { list-style: none; margin-top: 22px; }
  .contact-list li {
    display: flex; align-items: center; height: 29.5px;
    font-weight: 400; font-size: 17px; color: var(--white);
  }
  .contact-list svg { width: 15px; height: 15px; margin-right: 22px; fill: var(--orange); }

  .bottom-band { position: absolute; left: 0; bottom: 0; width: 708px; height: 18px; }
</style>
</head>
<body>

<section class="card card-front">
  <p class="brand-front">Pepper &amp; Palm</p>
</section>

<section class="card card-back">
  <p class="brand-back">Pepper &amp;<br>Palm</p>
  <div class="divider"></div>

  <div class="contact">
    <h1 class="contact-name">Jaswinder Bains (Ravi)</h1>
    <p class="contact-role">owner</p>
    <ul class="contact-list">
      <li>
        <svg viewBox="0 0 16 16" aria-hidden="true"><path d="M1 6c0-2 3-3 7-3s7 1 7 3v1h-4V5.5C10 5 6 5 5 5.5V7H1zM4 8h8l2 6H2z"/></svg>
        (480) 555-0147
      </li>
      <li>
        <svg viewBox="0 0 16 16" aria-hidden="true"><path d="M1 4h14v1L8 9 1 5zM1 6.5l7 4 7-4V13H1z"/></svg>
        RaviBains@postlark.com
      </li>
      <li>
        <svg viewBox="0 0 16 16" aria-hidden="true"><circle cx="8" cy="8" r="7"/><path d="M5 4c2 1 1 3 3 3s1 3 3 3" stroke="#1e1e1e" stroke-width="1.5" fill="none"/></svg>
        www.PepperPalmLV.com
      </li>
    </ul>
  </div>

  <svg class="bottom-band" viewBox="0 0 708 18" aria-hidden="true">
    <polygon points="0,0 376,0 366,18 0,18" fill="var(--orange)"/>
    <polygon points="382,0 708,0 708,18 372,18" fill="var(--white)"/>
  </svg>
</section>

</body>
</html>
```